Create a memorable Stationary for Security Software Company

Velbrantix is the worldwide leader in securing the Internet. Making Internet communications and critical data secure, reliable and available everywhere has been and continues to be our ongoing vision. We are committed to staying focused on real customer needs and to developing new and innovative security solutions that redefine the security landscape.

Industry/Entity Type

Internet

Font styles to use
Serif
Sans Serif
Script

Colors
0792cd
33a6d7
85cae6

```html
<!DOCTYPE html>
<html lang="en">
<head>
<meta charset="utf-8">
<title>Velbrantix Business Card</title>
<link href="https://fonts.googleapis.com/css2?family=Open+Sans:wght@400;600&display=swap" rel="stylesheet">
<style>
  :root {
    --blue-deep: #0792cd;
    --blue-mid: #33a6d7;
    --blue-light: #85cae6;
    --blue-pale: #b9e0f1;
    --ink: #0b5f8a;
    --ink-soft: #1f77a3;
    --backdrop: #e9edf0;
  }
  * { margin: 0; padding: 0; box-sizing: border-box; }
  html, body { width: 1200px; height: 843px; overflow: hidden; }
  body {
    background: var(--backdrop);
    font-family: "Open Sans", sans-serif;
    position: relative;
  }
  .card {
    position: absolute;
    width: 640px;
    height: 366px;
    border-radius: 22px;
    overflow: hidden;
    box-shadow: 0 6px 18px rgba(0, 40, 70, 0.18);
  }
  /* Back side */
  .card-back {
    left: 280px;
    top: 30px;
    background: linear-gradient(160deg, var(--blue-pale) 0%, var(--blue-light) 55%, var(--blue-mid) 100%);
  }
  .card-back .glow-band {
    position: absolute;
    left: 250px; top: 0;
    width: 60px; height: 100%;
    background: linear-gradient(90deg, rgba(255,255,255,0) 0%, rgba(255,255,255,0.35) 50%, rgba(255,255,255,0) 100%);
  }
  .card-back .brand {
    position: absolute;
    left: 0; right: 0; top: 128px;
    display: flex; align-items: center; justify-content: center; gap: 14px;
  }
  .card-back .brand-dot {
    width: 56px; height: 56px; border-radius: 50%;
    background: var(--blue-mid); opacity: 0.55;
  }
  .card-back .brand-name {
    font-weight: 600; font-size: 34px; color: var(--ink-soft); opacity: 0.75;
  }
  .card-back .web {
    position: absolute; left: 0; right: 0; bottom: 34px;
    text-align: center; font-size: 15px; letter-spacing: 6px; color: var(--ink-soft);
  }
  /* Front side */
  .card-front {
    left: 280px;
    top: 446px;
    background: linear-gradient(180deg, var(--blue-mid) 0%, var(--blue-deep) 100%);
  }
  .card-front .glow-band {
    position: absolute;
    left: 205px; top: 0;
    width: 50px; height: 100%;
    background: linear-gradient(90deg, rgba(255,255,255,0) 0%, rgba(255,255,255,0.22) 50%, rgba(255,255,255,0) 100%);
  }
  .card-front .cloud { position: absolute; inset: 0; }
  .contact {
    position: absolute; left: 44px; top: 34px; color: #fff;
  }
  .contact .person-name {
    font-size: 24px; font-weight: 600; color: var(--ink);
  }
  .contact .person-role {
    font-size: 16px; color: #fff; margin-top: 0;
  }
  .contact .address {
    font-size: 15px; line-height: 1.35; margin-top: 26px;
  }
  .contact .lines { list-style: none; margin-top: 6px; }
  .contact .lines li {
    display: flex; align-items: center; gap: 10px;
    font-size: 15px; line-height: 1.6;
  }
  .contact .lines svg { width: 15px; height: 15px; fill: var(--ink); flex: none; }
  .card-front .brand {
    position: absolute; left: 440px; top: 170px;
    display: flex; align-items: center; gap: 10px;
  }
  .card-front .brand-dot {
    width: 40px; height: 40px; border-radius: 50%; background: var(--blue-deep);
  }
  .card-front .brand-name {
    font-size: 26px; font-weight: 600; color: var(--blue-deep);
  }
</style>
</head>
<body>

<section class="card card-back" aria-label="Business card back">
  <div class="glow-band"></div>
  <div class="brand">
    <span class="brand-dot"></span>
    <span class="brand-name">Velbrantix</span>
  </div>
  <p class="web">www.velbrantix.net</p>
</section>

<section class="card card-front" aria-label="Business card front">
  <div class="glow-band"></div>
  <svg class="cloud" viewBox="0 0 640 366" width="640" height="366" aria-hidden="true">
    <path d="M640 46 L575 46 C555 12 500 10 478 44 C438 44 414 82 428 112 C392 128 388 178 418 198 C388 218 392 266 422 282 C406 312 424 346 452 366 L640 366 Z"
          fill="var(--blue-light)" stroke="#d6eef8" stroke-width="3"/>
  </svg>
  <div class="contact">
    <h1 class="person-name">Maren Toller</h1>
    <p class="person-role">CEO/Founder</p>
    <p class="address">4120 Larkfield Road<br>Juneau, Alaska 99801</p>
    <ul class="lines">
      <li><svg viewBox="0 0 16 16"><path d="M3.5 1.5l2.5 0 1.2 3-1.6 1.2a8 8 0 0 0 4.7 4.7l1.2-1.6 3 1.2v2.5c0 .8-.7 1.5-1.5 1.5A12.5 12.5 0 0 1 2 3c0-.8.7-1.5 1.5-1.5z"/></svg>555 201 4478</li>
      <li><svg viewBox="0 0 16 16"><path d="M4 1h8v4H4zM2 6h12c.6 0 1 .4 1 1v5h-3v3H4v-3H1V7c0-.6.4-1 1-1zm3 5v3h6v-3z"/></svg>555 318 0624</li>
      <li><svg viewBox="0 0 16 16"><path d="M1 3h14v10H1zm1.5 1.5v.4L8 8.6l5.5-3.7v-.4z"/></svg>hello@velbrantix.net</li>
      <li><svg viewBox="0 0 16 16"><path d="M8 1a7 7 0 1 0 0 14A7 7 0 0 0 8 1zm0 1.6c.9 1 1.5 2.5 1.7 4.6H6.3C6.5 5.1 7.1 3.6 8 2.6zM6.3 8.8h3.4c-.2 2.1-.8 3.6-1.7 4.6-.9-1-1.5-2.5-1.7-4.6zM2.7 7.2A5.4 5.4 0 0 1 5.2 3.3 9 9 0 0 0 4.7 7.2zm0 1.6h2a9 9 0 0 0 .5 3.9 5.4 5.4 0 0 1-2.5-3.9zm10.6-1.6h-2a9 9 0 0 0-.5-3.9 5.4 5.4 0 0 1 2.5 3.9zm0 1.6a5.4 5.4 0 0 1-2.5 3.9 9 9 0 0 0 .5-3.9z"/></svg>www.velbrantix.net</li>
    </ul>
  </div>
  <div class="brand">
    <span class="brand-dot"></span>
    <span class="brand-name">Velbrantix</span>
  </div>
</section>

</body>
</html>
```